Business Cards for new orthopaedic surgery practice

My husband and I are starting our own orthopaedic surgery practice. We are looking for a business card that is uniform, but one will have my name/title and the other will have his. You can just create one design with my name on it for now. But when I choose your design as the winning design I will ask that you add another copy with his name/title.

We are looking for classy, simple, elite all in one. We like dark blues/a little gold/yellow. Something that goes with our logo. We want our logo incorporated. Here is all the info you need:
Business name: RV Bone & Vitality Center
Location: 38517 North Willowmere Ave
Palm Hollow, FL 33990
Phone: 954-218-4063
Fax: 954-582-7341
Email: info@myrvbonecare.example

Names: Lydia Vance, M.D.
Board Certified Hand and Upper Extremity Surgeon

Ebo Dansu, M.D.
Board Certified Hip & Knee Replacement/General Orthopaedic Surgeon

Can decide what you want to put on the back. Maybe a slogan:
Rooted in Care. Focused on You

I am just going to upload our logo. The only thing is if we select you as the winning design, the location, and phone numbers may change. We will need your help to update that once fully solidified.

Industry/Entity Type

Medical

Contact Information for Business Card

Colors
0054AA
0677BA
7BADD7
CADEEF
E8F1F8
0094D4
00A9DD
6FCCEA
C7EBF8
E9F6FB

Requirements
Must have
• class, appeal,
Should not have
• We want to air on the side of masculine if we are looking at masculine vs. feminine feel. But we still want it classy, sophisticated, and something we will love

```html
<!DOCTYPE html>
<html lang="en">
<head>
<meta charset="utf-8">
<title>RV Bone &amp; Vitality Center – Business Card</title>
<link href="https://fonts.googleapis.com/css2?family=Outfit:wght@400;600;700&display=swap" rel="stylesheet">
<style>
  :root {
    --navy: #0d2b6e;
    --cyan: #22bfe3;
    --sky: #1aa9d6;
    --ribbon: #0996ee;
    --ribbon-deep: #0760c8;
    --white: #ffffff;
    --stage: #e9ebee;
  }
  * { margin: 0; padding: 0; box-sizing: border-box; }
  html, body { width: 1200px; height: 1200px; overflow: hidden; }
  body {
    background: var(--stage);
    font-family: "Outfit", sans-serif;
    position: relative;
  }
  .card {
    position: absolute;
    left: 242px;
    width: 716px;
    height: 397px;
    overflow: hidden;
  }

  /* Front */
  .card-front { top: 116px; background: var(--navy); }
  .front-name {
    position: absolute;
    top: 168px; left: 0; width: 100%;
    text-align: center;
    color: var(--white);
    font-weight: 600;
    font-size: 36px;
    line-height: 1;
    letter-spacing: 0.5px;
  }
  .front-sub {
    position: absolute;
    top: 228px; left: 0; width: 100%;
    display: flex; align-items: center; justify-content: center; gap: 10px;
    color: var(--white);
    font-weight: 600;
    font-size: 24px;
    line-height: 1;
    letter-spacing: 2px;
  }
  .front-sub::before, .front-sub::after {
    content: ""; width: 76px; height: 2px; background: var(--white);
  }
  .slogan-band {
    position: absolute;
    top: 302px; left: 0; width: 100%; height: 34px;
    background: var(--cyan);
    display: flex; align-items: center; justify-content: center;
  }
  .slogan {
    color: var(--navy);
    font-weight: 700;
    font-size: 18px;
  }

  /* Back */
  .card-back { top: 604px; background: var(--white); }
  .back-band {
    position: absolute;
    top: 146px; left: 0; width: 100%; height: 233px;
    background: var(--navy);
  }
  .ribbon { position: absolute; top: 0; left: 0; }
  .doctor-name {
    position: absolute; left: 58px; top: 34px;
    color: var(--navy);
    font-weight: 700;
    font-size: 21px;
    letter-spacing: 0.2px;
  }
  .doctor-title {
    position: absolute; left: 58px; top: 63px;
    color: var(--sky);
    font-size: 16.5px;
    line-height: 22px;
  }
  .back-name {
    position: absolute; left: 560px; top: 54px;
    color: var(--navy);
    font-weight: 600;
    font-size: 14px;
    line-height: 15px;
    letter-spacing: 0.5px;
  }
  .contact {
    position: absolute;
    color: var(--white);
    font-size: 16.5px;
    line-height: 23px;
    text-align: right;
  }
  .contact-phone { right: 551px; top: 248px; }
  .contact-fax { right: 551px; top: 300px; }
  .contact-email { right: 101px; top: 248px; }
  .contact-address { right: 99px; top: 290px; }
  .icon-box {
    position: absolute;
    width: 33px; height: 33px;
    border: 2px solid var(--white);
    display: flex; align-items: center; justify-content: center;
  }
  .icon-phone { left: 181px; top: 243px; }
  .icon-fax { left: 181px; top: 295px; }
  .icon-email { left: 632px; top: 242px; }
  .icon-home { left: 632px; top: 295px; }
</style>
</head>
<body>

  <section class="card card-front">
    <div class="front-name">RV BONE &amp; VITALITY</div>
    <div class="front-sub">CENTER</div>
    <div class="slogan-band"><p class="slogan">Grounded in Trust. Centered on You.</p></div>
  </section>

  <section class="card card-back">
    <div class="back-band"></div>
    <svg class="ribbon" width="716" height="397" viewBox="0 0 716 397">
      <polygon points="378,85 450,85 296,379 226,379" fill="var(--ribbon)"/>
      <polygon points="450,85 482,146 419,146" fill="var(--ribbon-deep)"/>
    </svg>

    <h1 class="doctor-name">LYDIA VANCE, M.D.</h1>
    <p class="doctor-title">Board Certified Hand and<br>Upper Extremity Surgeon</p>

    <div class="back-name">RV BONE &amp;<br>VITALITY<br>CENTER</div>

    <p class="contact contact-phone">954-218-4063</p>
    <div class="icon-box icon-phone">
      <svg width="16" height="22" viewBox="0 0 16 22"><rect x="2" y="1" width="12" height="20" rx="2" fill="none" stroke="#fff" stroke-width="2"/><rect x="5" y="4" width="6" height="11" fill="#fff"/></svg>
    </div>

    <p class="contact contact-fax">954-582-7341</p>
    <div class="icon-box icon-fax">
      <svg width="20" height="20" viewBox="0 0 20 20"><rect x="5" y="1" width="10" height="6" fill="none" stroke="#fff" stroke-width="2"/><rect x="1" y="7" width="18" height="8" rx="1" fill="none" stroke="#fff" stroke-width="2"/><rect x="5" y="12" width="10" height="7" fill="var(--navy)" stroke="#fff" stroke-width="2"/></svg>
    </div>

    <p class="contact contact-email">info@myrvbonecare.example</p>
    <div class="icon-box icon-email">
      <svg width="24" height="18" viewBox="0 0 24 18"><rect x="1" y="1" width="22" height="16" fill="none" stroke="#fff" stroke-width="1.6"/><polyline points="1,1 12,10 23,1" fill="none" stroke="#fff" stroke-width="1.6"/><line x1="1" y1="17" x2="9" y2="8" stroke="#fff" stroke-width="1.2"/><line x1="23" y1="17" x2="15" y2="8" stroke="#fff" stroke-width="1.2"/></svg>
    </div>

    <p class="contact contact-address">38517 North Willowmere Ave<br>Palm Hollow, FL 33990</p>
    <div class="icon-box icon-home">
      <svg width="22" height="20" viewBox="0 0 22 20"><polygon points="11,1 21,10 18,10 18,19 4,19 4,10 1,10" fill="#fff"/><rect x="8" y="12" width="6" height="5" fill="var(--navy)"/><line x1="11" y1="12" x2="11" y2="17" stroke="#fff" stroke-width="1"/><line x1="8" y1="14.5" x2="14" y2="14.5" stroke="#fff" stroke-width="1"/></svg>
    </div>
  </section>

</body>
</html>
```